Website development company website

ABOUT COMPANY
Hi everyone! We're a Melbourne, Australia website development company in a need of a website design that will make online store merchants want to engage our services.
We specialise exclusively in Torvista e-commerce platform (https://torvista-platform.example/). What distinguishes our business from competition is that rather than designing and building brand new websites, we offer development, support and maintenance services to established websites. Maintenance and Support are the keywords representing our business.
Our potential clients are people with broken, slow and underperforming Torvista installations who need assistance getting their websites up and making sales. Our website must pass the message that we can help, and provide quick means of making contact.
DESIGN
Overall, we're looking for a slick, clean, airy, conservative design. No need to do anything crazy, try to stick to what's "standard" in website design these days and make it easy on all of us. The website is unlikely to be updated too often so it needs to look attractive and fresh first time over and after a year, too.
Attached is our new logo, which you'll be able to take the basic idea from, the colors and fonts. Though, don't use the fonts from the logo in the website, stick to the standard widely supported fonts. Additional use of Google fonts is fine.
Don't overdo it with colors, stick to conservative basic color set and only use the colors from the log for accents like headings etc. Please, don't be tempted to use the blue and orange as background of whole blocks, other than perhaps footer. Thanks.
For the images used, I'd like to stay away from a design studio/digital agency feel and lean more towards professional support and maintenance services. I'm thinking images of content merchants doing their job. Something along the lines of "We'll be taking care of the website so that you only need to care about the business".
Some ideas I like:
http://www.plumframe-pics.example/detail/photo/portrait-of-confident-male-design-professional-royalty-free-image/572048163
http://www.plumframe-pics.example/detail/photo/designer-taking-picture-of-hat-high-res-stock-photography/839207514
http://www.plumframe-pics.example/detail/photo/woman-packaging-pottery-royalty-free-image/216684093
Images of colorful shopping bags and shopping carts are over the top and not serious enough. Instead of images matching Online Shopping, I'd try going more for Stability, Reliability, Performance.
Our existing website is http://www.bravuln.example. Please, don't take design ideas from it, but it will give you a picture of the structure of our new website and content that's going to be used initially.
If you could include a basic icon set to use throughout the website, that would be great. If the icons could match our logo (attached), it would be a big plus.
ALL PAGES
Every page must contain clearly visible phone number (1300 648 907) and a Contact Us Now button, which opens an AJAX driven popup form with Name, Email, Phone and Message to be sent through.
To start with, main menu items will be Torvista, Portfolio, Contact.
At the bottom of each page, please, include a newsletter subscription form with text Subscribe to Torvista Support and Security Updates.
For the footer, I'd like to see a logo strip with the following logos in grayscale (no need to link anywhere): Torvista, QRX, DataVane, NCB. You'll find the logos on Google Images.
Standard footer columns follow. Here, I'd like to see logos in color: Torvista Certified Developer, Torvista Ceritified Solution Provider. Again, the logos are on Google Images.
No social media logos/links necessary anywhere on the website.
...and then the copyright line.
FRONT PAGE
Large slider with images that would appeal to our target audience. Keywords here would be Torvista System Audit, Torvista Performance Optimisation, Torvista Website Emergency Recovery, Torvista Development Infrastructure Hosting. We'll have a static page created for each of these to link to.
In a corner of the slider, or on the edge, can I have an overlay with logos in color (same as footer): Torvista Certified Developer, Torvista Ceritified Solution Provider.
Underneath, a number of blocks, each with an image and teaser that we'll use to link to various pages throughout the website.
PORTFOLIO PAGE
I'm thinking a single long page with a block per client, which will contain project name, description from us and a testimonial from client. Also, each block will contain a single large screenshot. No gallery or slideshow is necessary here, just one image per project.
I'll leave the layout up to you, but try to put yourself in the shoes of a potential client reviewing our past work by simply scrolling down this one page.
CONTACT US PAGE
Separate page with the same form as above, phone number (1300 648 907), email address (support@kavreo.example), address (Suite 42, Level 3|8 Wattlebrook Lane|Fernvale Heights VIC 3999), and a grayscale Google Map.
CODING UP
Coding up into static HTML/CSS/JS is equally important as the design itself. We're a website development company, we'll be integrating the theme. We will spot any issues and we will point them out.
Coded up design must be fully responsive. Enough said.
To be able to create any content in future, we'd like one extra page coded up with samples of all themed elements, lists, forms, buttons, 2, 3, 4-column layout, alerts, icons, etc. This page does not need to be designed, only coded up.
The design will be integrated into Drupal using Twig. If possible at all, try to keep it in mind when designing and coding up, and make the integration into a Drupal theme easier for us.
GOOD LUCK!
That's it. Let me know if anything needs clarifying. So far I've had a great experience with ArtFlockly. I don't doubt some great designs will emerge. Clever ideas are highly appreciated, but also make it clear you've read and followed the points in this brief. Cheers, Tom

```html
<!DOCTYPE html>
<html lang="en">
<head>
<meta charset="utf-8">
<title>Kavreo — Torvista Development, Support &amp; Maintenance</title>
<link rel="stylesheet" href="https://fonts.googleapis.com/css2?family=Open+Sans:wght@300;400;600;700&display=swap">
<style>
:root{
  --navy:#0b3468;
  --navy-deep:#072a55;
  --orange:#e8781e;
  --ink:#333a44;
  --muted:#6b6f75;
  --line:#dfe1e4;
  --panel:#f3f2f2;
  --band:#eeeeef;
  --white:#ffffff;
  --logo-grey:#6d6e71;
}
*{box-sizing:border-box;margin:0;padding:0}
html,body{width:1200px;height:2736px;overflow:hidden}
body{position:relative;background:var(--white);font-family:"Open Sans",Arial,sans-serif;color:var(--ink)}
.abs{position:absolute}

/* top bar */
.topbar{left:0;top:0;width:1200px;height:28px;background:var(--navy-deep)}
.topbar .phone-pill{left:160px;top:3px;height:22px;padding:0 12px 0 6px;border:1px solid rgba(255,255,255,.7);border-radius:4px;color:#fff;font-size:12px;display:flex;align-items:center;gap:8px}
.topbar .phone-pill .dot{width:15px;height:15px;border-radius:50%;background:#fff;display:flex;align-items:center;justify-content:center}
.topbar .contact-now{right:160px;top:0;height:28px;display:flex;align-items:center;gap:7px;color:#fff;font-size:12px;font-weight:600}

/* header */
.header{left:0;top:28px;width:1200px;height:60px;background:#fff}
.brand{left:160px;top:10px;display:flex;align-items:center;gap:9px}
.brand .mark{width:30px;height:36px;background:var(--navy);border-radius:3px}
.brand .name{font-size:26px;font-weight:700;color:var(--orange);letter-spacing:-.5px}
.nav{right:160px;top:0;height:60px;display:flex;align-items:center;gap:28px;font-size:11.5px;text-transform:uppercase;color:#444}
.nav a{color:inherit;text-decoration:none;padding:6px 0}
.nav a.active{border-bottom:1px solid var(--ink)}

/* hero */
.hero{left:0;top:88px;width:1200px;height:454px;background:linear-gradient(180deg,#2c4f7e 0%,#4a6f9c 45%,#2a4b78 100%)}
.hero-photo{left:0;top:0;width:1200px;height:454px;background:radial-gradient(ellipse at 62% 50%,rgba(180,205,235,.55),rgba(20,50,95,0) 55%)}
.hero h1{left:160px;top:158px;font-weight:300;font-size:44px;line-height:54px;letter-spacing:.5px;text-transform:uppercase}
.hero h1 .accent{color:var(--orange);display:block}
.hero h1 .plain{color:#fff;display:block}
.badges{right:10px;bottom:12px;width:114px;height:83px;background:rgba(255,255,255,.75);display:flex;align-items:center;justify-content:center;gap:8px}
.badge{width:46px;height:70px;border-radius:3px}
.badge.grey{background:#d9dadc;border:2px solid #fff}
.badge.orange{background:var(--orange);border:2px solid #fff}
.slider-dots{left:560px;top:436px;display:flex;gap:4px}
.slider-dots span{width:16px;height:3px;background:var(--orange)}
.slider-dots span.on{background:#fff}

/* section titles */
.section-title{left:0;width:1200px;text-align:center;font-size:18px;font-weight:400;color:var(--ink);text-transform:uppercase;letter-spacing:.3px}
.ornament{left:0;width:1200px;display:flex;justify-content:center;align-items:center;gap:10px}
.ornament i{display:block;width:52px;height:1px;background:var(--orange)}
.ornament b{display:block;width:13px;height:13px;border-radius:50%;border:2px solid var(--orange)}

/* services */
.services{left:160px;top:630px;width:880px;height:400px}
.svc{position:absolute;width:293px;text-align:center;padding-top:12px}
.svc .icon{margin:0 auto 8px;width:66px;height:74px}
.svc h3{font-size:15px;font-weight:400;color:#222;margin-bottom:6px}
.svc p{font-size:11.5px;line-height:15px;color:#333;margin-bottom:8px}
.svc .more{display:inline-block;border:1px solid #555;font-size:9px;padding:3px 8px;color:#333;text-transform:uppercase}
.svc.featured{background:var(--orange);color:#fff;box-shadow:0 6px 22px rgba(0,0,0,.3)}
.svc.featured h3,.svc.featured p{color:#fff}
.svc.featured .more{border-color:#fff;color:#fff}
.grid-v{position:absolute;width:1px;background:var(--line)}
.grid-h{position:absolute;height:1px;background:var(--line)}

/* teaser rows */
.teaser{left:0;width:1200px;height:268px;display:flex}
.teaser .photo{width:608px;height:268px}
.teaser .copy{flex:1;background:var(--panel);padding:28px 26px 0 16px;font-size:10.6px;line-height:14.4px;color:#555;text-align:justify}
.teaser .copy p+p{margin-top:14px}

/* feature projects */
.projects-band{left:0;top:1862px;width:1200px;height:360px;background:var(--panel)}
.projects{left:160px;top:1888px;width:880px;height:304px}
.project{position:absolute;width:220px;height:152px;display:flex;align-items:center;justify-content:center;gap:8px;color:var(--logo-grey);font-weight:700;font-size:30px;letter-spacing:-.5px}
.project .sq{width:22px;height:22px;background:var(--logo-grey)}
.project .ci{width:22px;height:22px;border-radius:50%;background:var(--logo-grey)}

/* tech strip */
.tech{left:0;top:2262px;width:1200px;height:142px;background:var(--band);display:flex;align-items:center;justify-content:center}
.tech .item{width:220px;display:flex;align-items:center;justify-content:center;gap:8px;font-size:30px;font-weight:600;color:#555}
.tech .item .sq{width:24px;height:24px;background:#666}
.tech .item .ci{width:24px;height:24px;border-radius:50%;background:#666}

/* footer */
.footer{left:0;top:2444px;width:1200px;height:246px;background:var(--navy);color:#fff}
.fcol{position:absolute;top:22px;font-size:11px;line-height:15px}
.fcol h4{font-size:12px;font-weight:700;text-transform:uppercase;margin-bottom:14px;padding-bottom:5px;border-bottom:1px solid rgba(255,255,255,.6);display:inline-block}
.fcol h5{font-size:12px;font-weight:700;text-transform:uppercase;margin:10px 0 10px}
.fcol .row{display:flex;align-items:center;gap:12px}
.fbadges{display:flex;gap:12px;margin-top:12px}
.fbadges .badge{width:42px;height:74px}
.subscribe input{display:block;width:224px;height:30px;border:0;padding:0 8px;font-family:inherit;font-size:10px;color:#888;margin:24px 0 16px}
.subscribe button{background:var(--orange);border:0;color:#fff;font-family:inherit;font-size:10px;text-transform:uppercase;padding:8px 12px}
.bottombar{left:0;top:2690px;width:1200px;height:46px;background:var(--navy-deep);color:#fff;font-size:10px}
.bottombar .links{left:160px;top:0;height:46px;display:flex;align-items:center;gap:20px;text-transform:uppercase}
.bottombar .copy{right:160px;top:0;height:46px;display:flex;align-items:center}
</style>
</head>
<body>

<div class="abs topbar">
  <div class="abs phone-pill"><span class="dot"><svg width="9" height="9" viewBox="0 0 24 24"><path fill="#072a55" d="M6.6 10.8a15 15 0 006.6 6.6l2.2-2.2c.3-.3.7-.4 1-.2 1.1.4 2.3.6 3.6.6.6 0 1 .4 1 1V20c0 .6-.4 1-1 1A17 17 0 013 4c0-.6.4-1 1-1h3.5c.6 0 1 .4 1 1 0 1.3.2 2.5.6 3.6.1.3 0 .7-.2 1z"/></svg></span>1300 648 907</div>
  <div class="abs contact-now"><svg width="13" height="11" viewBox="0 0 24 20"><path fill="#fff" d="M2 2h14v9H7l-4 3v-3H2z M18 6h4v9h-1v3l-4-3h-7v-2h8z"/></svg>Contact Us Now</div>
</div>

<header class="abs header">
  <div class="abs brand"><span class="mark"></span><span class="name">Kavreo</span></div>
  <nav class="abs nav">
    <a class="active" href="#">Home</a><a href="#">Torvista</a><a href="#">Portfolio</a><a href="#">Contact</a>
  </nav>
</header>

<section class="abs hero">
  <div class="abs hero-photo" role="img" aria-label="Photo of a data centre aisle lined with server racks, tinted blue"></div>
  <h1 class="abs"><span class="accent">Torvista Development</span><span class="plain">Infrastructure Hosting.</span></h1>
  <div class="abs badges"><span class="badge grey"></span><span class="badge orange"></span></div>
  <div class="abs slider-dots"><span></span><span></span><span></span><span class="on"></span></div>
</section>

<h2 class="abs section-title" style="top:564px">What We Do</h2>
<div class="abs ornament" style="top:592px"><i></i><b></b><i></i></div>

<div class="abs services">
  <div class="grid-v" style="left:293px;top:190px;height:210px"></div>
  <div class="grid-v" style="left:586px;top:0;height:400px"></div>
  <div class="grid-h" style="left:0;top:190px;width:880px"></div>

  <div class="svc" style="left:0;top:0;height:190px">
    <svg class="icon" viewBox="0 0 66 74"><polygon points="33,2 63,19 63,55 33,72 3,55 3,19" fill="none" stroke="#e8781e" stroke-width="2.5"/><circle cx="33" cy="37" r="10" fill="none" stroke="#e8781e" stroke-width="4" stroke-dasharray="4 3"/><circle cx="33" cy="37" r="4" fill="#e8781e"/></svg>
    <h3>Torvista Development</h3><p>Lorem ipsum dolor sit amet,<br>consectetur adipiscing elit. Aliquam vehicula</p><span class="more">Read more ▸</span>
  </div>
  <div class="svc featured" style="left:292px;top:0;height:190px">
    <svg class="icon" viewBox="0 0 66 74"><polygon points="33,2 63,19 63,55 33,72 3,55 3,19" fill="#fff"/><circle cx="33" cy="30" r="7" fill="#e8781e"/><path d="M19 50h28v-4c0-5-6-8-14-8s-14 3-14 8z" fill="#e8781e"/></svg>
    <h3>Torvista Support</h3><p>Lorem ipsum dolor sit amet,<br>consectetur adipiscing elit. Aliquam vehicula</p><span class="more">Read more ▸</span>
  </div>
  <div class="svc" style="left:586px;top:0;height:190px">
    <svg class="icon" viewBox="0 0 66 74"><polygon points="33,2 63,19 63,55 33,72 3,55 3,19" fill="none" stroke="#e8781e" stroke-width="2.5"/><path d="M22 48l14-14" stroke="#e8781e" stroke-width="5" stroke-linecap="round"/><circle cx="40" cy="29" r="7" fill="none" stroke="#e8781e" stroke-width="4"/></svg>
    <h3>Torvista Maintenance</h3><p>Lorem ipsum dolor sit amet,<br>consectetur adipiscing elit. Aliquam vehicula</p><span class="more">Read more ▸</span>
  </div>

  <div class="svc" style="left:0;top:192px">
    <svg class="icon" viewBox="0 0 66 74"><polygon points="33,2 63,19 63,55 33,72 3,55 3,19" fill="none" stroke="#e8781e" stroke-width="2.5"/><ellipse cx="31" cy="26" rx="11" ry="4" fill="#e8781e"/><path d="M20 30v16c0 2 5 4 11 4" fill="none" stroke="#e8781e" stroke-width="3"/><circle cx="41" cy="45" r="6" fill="none" stroke="#e8781e" stroke-width="3"/></svg>
    <h3>Torvista Development</h3><p>Lorem ipsum dolor sit amet,<br>consectetur adipiscing elit. Aliquam vehicula</p><span class="more">Read more ▸</span>
  </div>
  <div class="svc" style="left:293px;top:192px">
    <svg class="icon" viewBox="0 0 66 74"><polygon points="33,2 63,19 63,55 33,72 3,55 3,19" fill="none" stroke="#e8781e" stroke-width="2.5"/><path d="M19 44a14 14 0 0128 0" fill="none" stroke="#e8781e" stroke-width="3"/><path d="M33 44l7-9" stroke="#e8781e" stroke-width="3" stroke-linecap="round"/></svg>
    <h3>Torvista Support</h3><p>Lorem ipsum dolor sit amet,<br>consectetur adipiscing elit. Aliquam vehicula</p><span class="more">Read more ▸</span>
  </div>
  <div class="svc" style="left:586px;top:192px">
    <svg class="icon" viewBox="0 0 66 74"><polygon points="33,2 63,19 63,55 33,72 3,55 3,19" fill="none" stroke="#e8781e" stroke-width="2.5"/><rect x="19" y="22" width="28" height="8" fill="#e8781e"/><rect x="19" y="33" width="28" height="8" fill="#e8781e"/><rect x="19" y="44" width="28" height="8" fill="#e8781e"/></svg>
    <h3>Torvista Maintenance</h3><p>Lorem ipsum dolor sit amet,<br>consectetur adipiscing elit. Aliquam vehicula</p><span class="more">Read more ▸</span>
  </div>
</div>

<h2 class="abs section-title" style="top:1068px">Variations of Passages</h2>
<div class="abs ornament" style="top:1096px"><i></i><b></b><i></i></div>
<section class="abs teaser" style="top:1136px">
  <div class="photo" role="img" aria-label="Photo of a designer at a bright studio desk photographing a hat" style="background:linear-gradient(100deg,#d9d4cc 0%,#bfb4a6 35%,#8a8f9a 60%,#e7e3dc 100%)"></div>
  <div class="copy">
    <p>Lorem ipsum dolor sit amet, consectetur adipiscing elit. Nullam eget risus lacus. Proin sollicitudin ultricies nunc, quis consequat enim. Vivamus fringilla quam dolor, quis dictum arcu viverra et. Class aptent taciti sociosqu ad litora torquent per conubia nostra, per inceptos himenaeos. Interdum et malesuada fames ac ante ipsum primis in faucibus. Donec orci ante, tincidunt id erat vestibulum, tempor semper libero. Nam tincidunt purus vitae dolor pharetra congue. Mauris vestibulum accumsan elit, nec rhoncus nibh varius eget. Nulla facilisi. Aenean bibendum, lectus non hendrerit fermentum, tortor mauris tristique mi, sed laoreet metus lacus et libero. In euismod eros ut laoreet semper. Suspendisse nec eros nec lacus volutpat feugiat in porta augue. Donec a consequat libero. In quis dui non libero vestibulum interdum purus a luctus eleifend.</p>
    <p>In hac habitasse platea dictumst. Fusce ac lectus finibus elit faucibus rutrum id eu ex. Praesent nec scelerisque velit. Nulla urna metus, pellentesque quis magna et, accumsan congue tortor. Nullam eget sem dapibus, molestie neque eget, ullamcorper ligula. Etiam non nisl orci. Maecenas efficitur nunc at ullamcorper hendrerit. Mauris arcu orci, pharetra sed magna sed, sagittis consectetur nisl. Morbi ut sem nec mi tincidunt euismod a id leo.</p>
  </div>
</section>

<h2 class="abs section-title" style="top:1434px">The Best Structure for You</h2>
<div class="abs ornament" style="top:1462px"><i></i><b></b><i></i></div>
<section class="abs teaser" style="top:1505px">
  <div class="photo" role="img" aria-label="Photo of a confident design professional in his workshop with pinned garments behind" style="background:linear-gradient(100deg,#6d5a48 0%,#a08a72 40%,#4aa3c4 70%,#d7d0c6 100%)"></div>
  <div class="copy">
    <p>Lorem ipsum dolor sit amet, consectetur adipiscing elit. Nullam eget risus lacus. Proin sollicitudin ultricies nunc, quis consequat enim. Vivamus fringilla quam dolor, quis dictum arcu viverra et. Class aptent taciti sociosqu ad litora torquent per conubia nostra, per inceptos himenaeos. Interdum et malesuada fames ac ante ipsum primis in faucibus. Donec orci ante, tincidunt id erat vestibulum, tempor semper libero. Nam tincidunt purus vitae dolor pharetra congue. Mauris vestibulum accumsan elit, nec rhoncus nibh varius eget. Nulla facilisi. Aenean bibendum, lectus non hendrerit fermentum, tortor mauris tristique mi, sed laoreet metus lacus et libero. In euismod eros ut laoreet semper. Suspendisse nec eros nec lacus volutpat feugiat in porta augue. Donec a consequat libero. In quis dui non libero vestibulum interdum purus a luctus eleifend.</p>
    <p>In hac habitasse platea dictumst. Fusce ac lectus finibus elit faucibus rutrum id eu ex. Praesent nec scelerisque velit. Nulla urna metus, pellentesque quis magna et, accumsan congue tortor. Nullam eget sem dapibus, molestie neque eget, ullamcorper ligula. Etiam non nisl orci. Maecenas efficitur nunc at ullamcorper hendrerit. Mauris arcu orci, pharetra sed magna sed, sagittis consectetur nisl. Morbi ut sem nec mi tincidunt euismod a id leo.</p>
  </div>
</section>

<h2 class="abs section-title" style="top:1800px">Feature Projects</h2>
<div class="abs ornament" style="top:1828px"><i></i><b></b><i></i></div>
<div class="abs projects-band"></div>
<div class="abs projects">
  <div class="grid-v" style="left:220px;top:0;height:304px"></div>
  <div class="grid-v" style="left:440px;top:0;height:304px"></div>
  <div class="grid-v" style="left:660px;top:0;height:304px"></div>
  <div class="grid-h" style="left:0;top:152px;width:880px"></div>
  <div class="project" style="left:0;top:0"><span class="sq"></span>FUNDLOOP</div>
  <div class="project" style="left:220px;top:0"><span class="ci"></span>helpwick</div>
  <div class="project" style="left:440px;top:0"><span class="ci"></span>meshmill</div>
  <div class="project" style="left:660px;top:0"><span class="sq"></span>Rentova</div>
  <div class="project" style="left:0;top:152px">quickra</div>
  <div class="project" style="left:220px;top:152px;font-size:24px">NODEVALE</div>
  <div class="project" style="left:440px;top:152px">Clipnest</div>
  <div class="project" style="left:660px;top:152px;font-size:24px">MERIDEN &amp; CO</div>
</div>

<div class="abs tech">
  <div class="item"><span class="sq"></span>Torvista</div>
  <div class="item"><span class="ci"></span>QRX</div>
  <div class="item">DataVane</div>
  <div class="item"><span class="sq"></span>NCB</div>
</div>

<footer class="abs footer">
  <div class="fcol" style="left:160px;width:240px">
    <h4>About Us</h4>
    <p style="text-align:justify">Torvista, fully owned by Norbay Inc., is one of the most popular eCommerce platforms. It offers flexible, scalable eCommerce solutions designed to help businesses grow and succeed online. The Torvista platform is trusted by more than 150,000 businesses, including some of the world's leading brands.</p>
    <div class="fbadges"><span class="badge grey"></span><span class="badge orange"></span></div>
  </div>
  <div class="fcol" style="left:461px;width:240px">
    <h4>Address</h4>
    <p>Suite 42, Level 3<br>8 Wattlebrook Lane<br>Fernvale Heights VIC 3999</p>
    <h5>Phone</h5>
    <div class="row"><svg width="10" height="10" viewBox="0 0 24 24"><path fill="#fff" d="M6.6 10.8a15 15 0 006.6 6.6l2.2-2.2c.3-.3.7-.4 1-.2 1.1.4 2.3.6 3.6.6.6 0 1 .4 1 1V20c0 .6-.4 1-1 1A17 17 0 013 4c0-.6.4-1 1-1h3.5c.6 0 1 .4 1 1 0 1.3.2 2.5.6 3.6.1.3 0 .7-.2 1z"/></svg>1300 552 814</div>
    <h5 style="margin-top:22px">Email ID</h5>
    <div class="row"><svg width="11" height="9" viewBox="0 0 24 18"><rect x="1" y="1" width="22" height="16" rx="2" fill="#fff"/><path d="M2 2l10 8 10-8" fill="none" stroke="#0b3468" stroke-width="2"/></svg>support@kavreo.example</div>
  </div>
  <div class="fcol subscribe" style="left:762px;width:280px">
    <h4>Newsletter Subscription</h4>
    <p>Subscribe to Torvista Support and Security Updates.</p>
    <input type="text" placeholder="Email id">
    <button type="button">Subscribe</button>
  </div>
</footer>

<div class="abs bottombar">
  <div class="abs links"><span>Home</span><span>Torvista</span><span>Portfolio</span><span>Contact</span></div>
  <div class="abs copy">Copyright 2016 kavreo.example. All rights reserved</div>
</div>

</body>
</html>
```